Brin U's Jar Lable for kids Christmas gifts

Looking to get a wrap around label made for a quart canning jar. I would like it to have my kids head on it also. I was thinking in a silhouette form on both ends of the wrap( added a quick sketch up). We will be canning Pickles and giving them away as gifts this year. Also might be selling a few at a frames market. The brand name is " Brin U's" ( at the moment) So if you could think of a cool logo around that would be awesome also. I am an Orange and Black fan but I am up for suggestions also. Do you think this might be something you could help me with?

The second attached graphic is what I would like my kids faces to look similer to. Art wise. The sketch is of what the ends of the labels need to look like. Not a full face but a half of each of there faces on both ends of the lable.

Colors
f78f20
000000
757575

Requirements
Nice to have
• antique lable feel

```html
<!DOCTYPE html>
<html lang="en">
<head>
<meta charset="UTF-8">
<title>Brin U's Jar Label</title>
<link href="https://fonts.googleapis.com/css2?family=Oswald:wght@400;500;700&display=swap" rel="stylesheet">
<style>
  :root {
    --orange: #f78f20;
    --black: #000000;
    --white: #ffffff;
    --page: #e6e7ea;
    --art-tone: #e7a66f;
  }
  * { margin: 0; padding: 0; box-sizing: border-box; }
  html, body {
    width: 1200px; height: 1200px; overflow: hidden;
    background: var(--page);
    font-family: 'Oswald', sans-serif;
  }
  .label {
    position: absolute;
    left: 41px; top: 341px;
    width: 1118px; height: 558px;
    background: var(--orange);
    overflow: hidden;
  }
  .art-slot {
    position: absolute;
    top: 72px; width: 228px; height: 443px;
    background: var(--art-tone);
  }
  .art-slot--left { left: 0; }
  .art-slot--right { right: 0; }

  .panel {
    position: absolute;
    background: var(--black);
    color: var(--white);
    border-radius: 8px;
    font-weight: 500;
    text-transform: uppercase;
    white-space: nowrap;
  }
  .panel--tall {
    left: 269px; top: 49px; width: 254px; height: 461px;
    display: flex; justify-content: center; align-items: flex-start;
    padding-top: 24px;
  }
  .panel--tall .panel__copy {
    writing-mode: vertical-rl;
    font-size: 22px;
    line-height: 29px;
    letter-spacing: 0.3px;
  }
  .panel--small {
    left: 584px; top: 301px; width: 255px; height: 209px;
    display: flex; align-items: center; justify-content: center;
    text-align: center;
    font-size: 22px; line-height: 28px; letter-spacing: 0.3px;
  }

  .brand-frame {
    position: absolute;
    left: 563px; top: 55px; width: 294px; height: 179px;
    border: 2px dashed var(--white);
    border-radius: 8px;
  }
  .brand-frame__inner {
    position: absolute;
    left: 14px; top: 14px; right: 14px; bottom: 14px;
    border: 2px dashed var(--white);
    border-radius: 6px;
    display: flex; align-items: center; justify-content: center;
  }
  .brand-name {
    font-weight: 700;
    font-size: 64px;
    color: var(--white);
    letter-spacing: 1px;
    white-space: nowrap;
  }
</style>
</head>
<body>
  <main class="label">
    <div class="art-slot art-slot--left" role="img" aria-label="Cartoon illustration of a smiling child's half face, left end of the wrap"></div>

    <section class="panel panel--tall">
      <p class="panel__copy">Your text your text your text your text<br>Your text your text your text your text<br>Your text your text your text your text<br>Your text your text your text your text<br>Your text your text your text your text<br>Your text your text your text your text</p>
    </section>

    <div class="brand-frame">
      <div class="brand-frame__inner">
        <span class="brand-name">Brin U's</span>
      </div>
    </div>

    <section class="panel panel--small">
      <p>Your text your text<br>Your text your text<br>Your text your text<br>Your text your text<br>Your text your text<br>Your text your text</p>
    </section>

    <div class="art-slot art-slot--right" role="img" aria-label="Cartoon illustration of a smiling child's half face, right end of the wrap"></div>
  </main>
</body>
</html>
```